Business cards for Norwegian software consultancy business

We are in need of business cards for our Norwegian consultancy company.
“Valto Brindex AS” specializes in software development, architecture and agile methodology, providing mostly on-site services at customers.
The cards should reflect a certain level of business professionalism with an elegant touch, while paying tribute to our modern and technological heritage. Our logo should be featured, as well as room for basic information about the cardholder and legal information of the company (company name, address and VAT number).
We would like our cards to reflect that we are a modern consulting company. It should present a professional image that people will remember. The texture and color pallette should reflect our professionalism and reliability, so we prefer a light color pallette with colors such as gray, white, blue and black. The number of colors used should however not be overwhelming, with the text being distinct and readable.
We are open to untraditional layouts and playful designs as long as they communicate the intent stated above.
You could also take a look at our website http://www.brindex.no for input on our visual profile.
Our logo is attached in the form of vectors and rasterized PNG. Please comment if you would like the black-white and/or inverted versions as well.
Industry/Entity Type
Architecture
Contact Information for Business Card
Company information:
Valto Brindex AS
Kvernlia 14, 3170 Sem
482 71 519
info@brindex.no
www.brindex.no
Employee information:
Full name
Title
Email
Phone
Font styles to use
Look and feel

```html
<!DOCTYPE html>
<html lang="no">
<head>
<meta charset="utf-8">
<title>Valto Brindex AS – Business Cards</title>
<link rel="stylesheet" href="https://fonts.googleapis.com/css2?family=Rajdhani:wght@400;500;700&display=swap">
<style>
  :root {
    --backdrop: #6f7878;
    --card-white: #ffffff;
    --card-black: #0b0b0b;
    --gold: #b8962e;
    --gold-light: #c9a73c;
    --card-shadow: 0 14px 30px rgba(0, 0, 0, 0.35);
  }
  * { box-sizing: border-box; margin: 0; padding: 0; }
  html, body {
    width: 1200px;
    height: 900px;
    overflow: hidden;
  }
  body {
    background: var(--backdrop);
    font-family: "Rajdhani", sans-serif;
    display: flex;
    flex-direction: column;
    align-items: center;
    justify-content: center;
    gap: 50px;
  }
  .card {
    position: relative;
    width: 580px;
    height: 330px;
    border-radius: 26px;
    background: var(--card-white);
    overflow: hidden;
    box-shadow: var(--card-shadow);
  }
  .card__circle {
    position: absolute;
    border-radius: 50%;
    background: var(--card-black);
  }
  /* Back side: contact details */
  .card--back .card__circle {
    width: 430px;
    height: 430px;
    left: -40px;
    top: -50px;
  }
  .contact {
    position: absolute;
    left: 68px;
    top: 52px;
    color: var(--gold);
    line-height: 1.15;
  }
  .contact__name {
    font-size: 25px;
    font-weight: 500;
    letter-spacing: 1px;
  }
  .contact__title {
    font-size: 19px;
    font-weight: 700;
    margin-bottom: 14px;
  }
  .contact__list { list-style: none; }
  .contact__item {
    display: flex;
    align-items: center;
    gap: 12px;
    font-size: 19px;
    font-weight: 500;
    letter-spacing: 0.6px;
  }
  .contact__icon {
    width: 16px;
    height: 16px;
    flex: none;
  }
  .company {
    margin-top: 4px;
    font-size: 19px;
    letter-spacing: 0.6px;
  }
  .company__name { font-weight: 700; }
  .company__line { font-weight: 500; }

  .brand {
    position: absolute;
    display: flex;
    align-items: center;
    gap: 12px;
    color: var(--gold);
    font-weight: 500;
    text-transform: uppercase;
    white-space: nowrap;
  }
  .brand__mark {
    background: var(--gold);
    flex: none;
  }
  .card--back .brand {
    right: 48px;
    top: 74px;
    font-size: 26px;
    letter-spacing: 3px;
  }
  .card--back .brand__mark { width: 20px; height: 20px; }

  /* Front side: brand */
  .card--front .card__circle {
    width: 470px;
    height: 470px;
    left: 120px;
    top: -70px;
  }
  .card--front .brand {
    left: 185px;
    top: 144px;
    font-size: 36px;
    letter-spacing: 4px;
  }
  .card--front .brand__mark { width: 28px; height: 28px; }
</style>
</head>
<body>

  <section class="card card--back" aria-label="Card back with contact details">
    <div class="card__circle"></div>
    <div class="contact">
      <p class="contact__name">Lina Haugrud</p>
      <p class="contact__title">Co-Founder &amp; CEO</p>
      <ul class="contact__list">
        <li class="contact__item">
          <svg class="contact__icon" viewBox="0 0 16 16" fill="none" stroke="currentColor" stroke-width="1.5">
            <rect x="4" y="1.5" width="8" height="13" rx="1.2"/>
            <line x1="7" y1="12" x2="9" y2="12"/>
          </svg>
          (047) 555-0192
        </li>
        <li class="contact__item">
          <svg class="contact__icon" viewBox="0 0 16 16" fill="none" stroke="currentColor" stroke-width="1.5">
            <rect x="1.5" y="3.5" width="13" height="9"/>
            <polyline points="1.5,3.5 8,9 14.5,3.5"/>
          </svg>
          info@brindex.no
        </li>
        <li class="contact__item">
          <svg class="contact__icon" viewBox="0 0 16 16" fill="none" stroke="currentColor" stroke-width="1.3">
            <circle cx="8" cy="8" r="6.5"/>
            <ellipse cx="8" cy="8" rx="3" ry="6.5"/>
            <line x1="1.5" y1="8" x2="14.5" y2="8"/>
          </svg>
          brindex.no
        </li>
      </ul>
      <div class="company">
        <p class="company__name">Valto Brindex AS</p>
        <p class="company__line">Kvernlia 14</p>
        <p class="company__line">3170 Sem</p>
      </div>
    </div>
    <div class="brand">
      <span class="brand__mark"></span>
      <span class="brand__name">Valto Brindex</span>
    </div>
  </section>

  <section class="card card--front" aria-label="Card front with company name">
    <div class="card__circle"></div>
    <div class="brand">
      <span class="brand__mark"></span>
      <span class="brand__name">Valto Brindex</span>
    </div>
  </section>

</body>
</html>
```